Quillmere Supply Chain and Logistic Consulting

Please review the attached Business Card. I want as close to this card with the colors, fonts, and quality of the card as possible. The attached compass should replace the deer head on both sides of the card and the text should say:

Backside
Compass JPEG
Quillmere Logistics
A Supply Chain and Logistics Consulting Company

Frontside
Quillmere Logistics
Ray Falkner - Harrowgate Ohio
President
____________________________________
(555) 314-9027
QuillmereSCL@Examplemail.com
_____________________________________

Bottom Front Side

Target Market(s)

Businesses

Contact Information for Business Card

Backside
Compass JPEG
Quillmere Logistics

Frontside
Quillmere Logistics
President
(555) 314-9027
QuillmereSCL@Examplemail.com

Bottom Front Side

Font styles to use
Serif
Script

Colors

Designer to choose colors to be used in the design.

Requirements
Must have
• See attached card for reference
Nice to have
Should not have

```html
<!DOCTYPE html>
<html lang="en">
<head>
<meta charset="UTF-8">
<title>Quillmere Logistics — Business Card</title>
<link rel="stylesheet" href="https://fonts.googleapis.com/css2?family=Crimson+Text:wght@400;600&display=swap">
<style>
  :root {
    --backdrop: #2b2c30;
    --card: #ffffff;
    --navy: #1c2a4a;
    --steel: #5f7898;
    --mist: #e4e6ea;
    --ink: #1f2533;
  }
  * { box-sizing: border-box; margin: 0; padding: 0; }
  html, body { width: 1200px; height: 800px; overflow: hidden; }
  body {
    background: var(--backdrop);
    position: relative;
    font-family: "Crimson Text", Georgia, serif;
    color: var(--ink);
  }
  .card {
    position: absolute;
    width: 540px;
    height: 310px;
    background: var(--card);
    border-radius: 22px;
    overflow: hidden;
    box-shadow: 0 18px 40px rgba(0,0,0,0.45);
  }
  .card--back { left: 40px; top: 245px; }
  .card--front { left: 620px; top: 245px; }

  /* Back side */
  .brand-mark {
    position: absolute;
    left: 50%; top: 34px;
    width: 150px; height: 150px;
    margin-left: -75px;
    border-radius: 50%;
    background: var(--steel);
  }
  .back-wordmark {
    position: absolute;
    left: 0; right: 0; top: 196px;
    text-align: center;
    font-weight: 400;
    font-size: 36px;
    line-height: 1.2;
    color: var(--navy);
  }
  .back-tagline {
    position: absolute;
    left: 0; right: 0; top: 246px;
    text-align: center;
    font-size: 15px;
    color: var(--navy);
  }

  /* Front side */
  .faint-circle {
    position: absolute;
    right: -90px; top: -110px;
    width: 300px; height: 300px;
    border-radius: 50%;
    background: var(--mist);
    opacity: 0.8;
  }
  .front-info {
    position: absolute;
    left: 30px; top: 38px;
    width: 320px;
    text-align: center;
  }
  .front-wordmark {
    font-weight: 400;
    font-size: 28px;
    color: var(--navy);
    line-height: 1.1;
  }
  .front-tagline {
    font-size: 12.5px;
    color: var(--navy);
    margin-top: 2px;
  }
  .person {
    font-size: 20px;
    color: var(--navy);
    margin-top: 10px;
    line-height: 1.2;
  }
  .role {
    font-size: 14px;
    color: var(--navy);
  }
  .rule {
    height: 1.5px;
    background: var(--navy);
    margin: 8px auto;
    width: 260px;
  }
  .contact {
    font-size: 15px;
    line-height: 1.35;
    color: var(--ink);
  }
  .footer-line {
    position: absolute;
    left: 30px; right: 30px; bottom: 26px;
    display: flex;
    align-items: center;
    gap: 12px;
    font-size: 13px;
    color: var(--navy);
    white-space: nowrap;
  }
  .footer-line::before,
  .footer-line::after {
    content: "";
    flex: 1;
    height: 1.5px;
    background: var(--navy);
  }
</style>
</head>
<body>
  <section class="card card--back" aria-label="Card back">
    <div class="brand-mark" aria-hidden="true"></div>
    <h1 class="back-wordmark">Quillmere Logistics</h1>
    <p class="back-tagline">A Supply Chain and Logistics Consulting Company</p>
  </section>

  <section class="card card--front" aria-label="Card front">
    <div class="faint-circle" aria-hidden="true"></div>
    <div class="front-info">
      <h2 class="front-wordmark">Quillmere Logistics</h2>
      <p class="front-tagline">A Supply Chain and Logistics Consulting Company</p>
      <p class="person">Ray Falkner &bull; Harrowgate Ohio</p>
      <p class="role">President</p>
      <div class="rule"></div>
      <p class="contact">(555) 314-9027<br>QuillmereSCL@Examplemail.com</p>
      <div class="rule"></div>
    </div>
    <p class="footer-line">A Supply Chain and Logistics Consulting Company</p>
  </section>
</body>
</html>
```